Business Card Design

Tumble Harbor is a Laundromat Store
we provide wash and Fold service to Customers who are busy with their life and can not come to the store and do laundry
we have customers who drop their laundry at the store
but now i want to provide service to customers who are not able to come to the store to drop. i will go to their address and pickup the laundry and get it washed folded and delivered
Updates
Can you use the colour in you design which i uploaded and also fusha fluorescent green bright pink
Target Market(s)
all works of life who don't have time to do laundry
Industry/Entity Type
Store
Contact Information for Business Card
TumbleHarbor Laundromat
247 Mallory Street
Lynn MA 01938
Look and feel
Each slider illustrates characteristics of the customer's brand and the style your logo design should communicate.

```html
<!DOCTYPE html>
<html lang="en">
<head>
<meta charset="utf-8">
<title>TumbleHarbor Laundromat – Business Card</title>
<link rel="stylesheet" href="https://fonts.googleapis.com/css2?family=Montserrat:wght@600;700;800&family=Open+Sans:wght@600;700&display=swap">
<style>
  :root {
    --backdrop: #2e2e2e;
    --fuchsia: #ec1a8c;
    --fuchsia-deep: #c3127a;
    --plum: #a02a8f;
    --green: #1fa45b;
    --green-deep: #0f7a42;
    --white: #ffffff;
    --pile-warm: #c78aa6;
    --pile-stack: #8d5a52;
  }
  html, body {
    margin: 0;
    width: 1200px;
    height: 900px;
    overflow: hidden;
    background: var(--backdrop);
  }
  .card {
    position: absolute;
    left: 80px;
    top: 150px;
    width: 1040px;
    height: 600px;
    overflow: hidden;
    background: var(--fuchsia);
    color: var(--white);
    font-family: "Montserrat", sans-serif;
  }
  .card__band {
    position: absolute;
    inset: 0;
  }
  .brand {
    position: absolute;
    top: 52px;
    left: 0;
    width: 100%;
    display: flex;
    justify-content: center;
    align-items: center;
    gap: 14px;
    font-family: "Open Sans", sans-serif;
    font-weight: 700;
    font-size: 44px;
    letter-spacing: 0.5px;
  }
  .brand__dot {
    width: 22px;
    height: 22px;
    border-radius: 50%;
    background: var(--white);
  }
  .address {
    position: absolute;
    top: 118px;
    width: 100%;
    text-align: center;
    font-weight: 700;
    font-size: 25px;
    letter-spacing: 3px;
    text-transform: uppercase;
  }
  .phone {
    position: absolute;
    top: 160px;
    left: 50%;
    transform: translateX(-50%);
    background: var(--plum);
    padding: 5px 14px;
    font-weight: 700;
    font-size: 24px;
    white-space: nowrap;
  }
  .laundry {
    position: absolute;
    top: 215px;
    height: 140px;
    border-radius: 40px 40px 8px 8px;
  }
  .laundry--before {
    left: 330px;
    width: 170px;
    background: radial-gradient(circle at 45% 40%, #e9b8cf, var(--pile-warm) 60%, #9c6a84);
  }
  .laundry--after {
    left: 560px;
    width: 170px;
    border-radius: 6px;
    background: linear-gradient(#5b3b3a, #b04a4a 25%, #3d5a3c 45%, #7a3a6a 65%, #c7a06a 85%, var(--pile-stack));
  }
  .swap-badge {
    position: absolute;
    left: 440px;
    top: 200px;
    width: 150px;
    height: 150px;
    border-radius: 50%;
    background: var(--plum);
    border: 3px solid var(--white);
  }
  .swap-badge__from, .swap-badge__to {
    position: absolute;
    font-weight: 700;
    font-size: 24px;
  }
  .swap-badge__from { left: 40px; top: 30px; }
  .swap-badge__to { left: 50px; top: 82px; }
  .swap-badge svg { position: absolute; left: 0; top: 0; }
  .steps {
    position: absolute;
    left: 0;
    top: 395px;
    width: 100%;
    height: 205px;
  }
  .step {
    position: absolute;
    width: 220px;
    margin-left: -110px;
    text-align: center;
    font-family: "Open Sans", sans-serif;
    font-weight: 700;
    font-size: 19px;
    line-height: 1.25;
  }
  .step__icon {
    width: 104px;
    height: 104px;
    margin: 0 auto 10px;
    border-radius: 50%;
    background: var(--white);
    display: flex;
    align-items: center;
    justify-content: center;
  }
  .step__art {
    width: 72px;
    height: 72px;
    border-radius: 50%;
  }
  .step--schedule { left: 150px; top: 0; }
  .step--pickup { left: 415px; top: -28px; }
  .step--wash { left: 685px; top: -38px; }
  .step--enjoy { left: 915px; top: -48px; }
  .step--schedule .step__art { background: linear-gradient(#e3e3e3, #8a8a8a); }
  .step--pickup .step__art { background: linear-gradient(#6db7f0, #e45a3c); }
  .step--wash .step__art { background: linear-gradient(#7fc6d9, #6b6b6b); }
  .step--enjoy .step__art { background: radial-gradient(#ffe94d, #f4b400); }
  .flow-arrows { position: absolute; left: 0; top: 0; }
</style>
</head>
<body>
  <main class="card">
    <svg class="card__band" width="1040" height="600" viewBox="0 0 1040 600" aria-hidden="true">
      <defs>
        <linearGradient id="bandGreen" x1="0" y1="0" x2="0" y2="1">
          <stop offset="0" stop-color="var(--green)"/>
          <stop offset="1" stop-color="var(--green-deep)"/>
        </linearGradient>
      </defs>
      <path d="M0 385 Q520 255 1040 385 L1040 600 L0 600 Z" fill="url(#bandGreen)"/>
      <path d="M0 385 Q520 255 1040 385" fill="none" stroke="var(--white)" stroke-width="5"/>
    </svg>

    <div class="brand"><span class="brand__dot"></span>TumbleHarbor LAUNDROMAT</div>
    <div class="address">247 Mallory Street Lynn MA 01938</div>
    <div class="phone">CALL US: 079 555 01234</div>

    <div class="laundry laundry--before" role="img" aria-label="Pile of crumpled dirty laundry"></div>
    <div class="laundry laundry--after" role="img" aria-label="Neat stack of folded clean clothes"></div>

    <div class="swap-badge">
      <span class="swap-badge__from">FROM</span>
      <span class="swap-badge__to">TO</span>
      <svg width="150" height="150" viewBox="0 0 150 150" aria-hidden="true">
        <g fill="none" stroke="var(--white)" stroke-width="2">
          <path d="M120 66 H32 M40 59 L32 66 L40 73"/>
          <path d="M30 118 H118 M110 111 L118 118 L110 125"/>
        </g>
      </svg>
    </div>

    <section class="steps">
      <svg class="flow-arrows" width="1040" height="205" viewBox="0 0 1040 205" aria-hidden="true">
        <g fill="none" stroke="var(--white)" stroke-width="3" stroke-linecap="round">
          <path d="M225 55 Q290 30 335 28"/>
          <path d="M325 20 L337 28 L326 37"/>
          <path d="M490 40 Q555 10 600 15"/>
          <path d="M590 7 L602 15 L591 24"/>
          <path d="M760 28 Q800 5 835 5"/>
          <path d="M825 -3 L837 5 L826 14"/>
        </g>
      </svg>
      <div class="step step--schedule">
        <div class="step__icon"><div class="step__art" role="img" aria-label="Schedule calendar icon"></div></div>
        You Schedule<br>A Pick-Up
      </div>
      <div class="step step--pickup">
        <div class="step__icon"><div class="step__art" role="img" aria-label="House icon"></div></div>
        We Pick-Up<br>Your Dirty Laundry
      </div>
      <div class="step step--wash">
        <div class="step__icon"><div class="step__art" role="img" aria-label="Washing machines and laundry icon"></div></div>
        We Wash, Dry, Fold<br>&amp; Return Clean Laundry
      </div>
      <div class="step step--enjoy">
        <div class="step__icon"><div class="step__art" role="img" aria-label="Happy customer thumbs-up icon"></div></div>
        Enjoy Effortless<br>Clean Laundry
      </div>
    </section>
  </main>
</body>
</html>
```